Social Media App Needs PPT Template

We need a PowerPoint template for a new social media company based in the DC area called "Bold Ledger." We provide an interactive digital platform for executives to share actionable advice. We would like to see designs that use our orange logo color as an accent, but are mainly grey, white, and black. The final design should communicate clean, chic, modern, and professional.

Target Market(s)

Executives

Industry/Entity Type

Information Technology

Font styles to use
Sans Serif

Colors
f78f20
fbe7d2
ffffff
000000
e8e8e8
757575

Requirements
Must have
• My project must have title page and many options for the body of the ppt (graphs, tables, etc). It also needs to be easy to modify. I must have someone who is experienced in creating powerpoint templates.
Nice to have
• It would be nice to have a very modern and clean design that includes the logo on every page, but still leaves a lot of room for the content of the slide
Should not have
• My design project should not look to busy.

```html
<!DOCTYPE html>
<html lang="en">
<head>
<meta charset="utf-8">
<title>Bold Ledger – Content Slide</title>
<link href="https://fonts.googleapis.com/css2?family=Lato:wght@300;400;700&display=swap" rel="stylesheet">
<style>
  :root {
    --stage: #545454;
    --orange: #e8861c;
    --orange-light: #f2961f;
    --navy: #232a3b;
    --slide-light: #ffffff;
    --slide-edge: #ebebec;
    --placeholder: #cdced0;
    --placeholder-text: #e4e5e7;
    --body-text: #444448;
    --footer-text: #d8dbe2;
    --white: #ffffff;
  }
  * { margin: 0; padding: 0; box-sizing: border-box; }
  html, body {
    width: 1200px; height: 960px; overflow: hidden;
    background: var(--stage);
    font-family: "Lato", Arial, sans-serif;
  }
  .page-label {
    position: absolute; top: 72px; left: 0; width: 1172px;
    text-align: center; color: var(--white);
    font-weight: 300; font-size: 28px;
  }
  .slide {
    position: absolute; left: 111px; top: 134px;
    width: 970px; height: 728px; overflow: hidden;
    background: radial-gradient(ellipse at 45% 35%, var(--slide-light) 0%, #f6f6f7 50%, var(--slide-edge) 100%);
  }
  .slide-chrome { position: absolute; inset: 0; }
  .slide-title {
    position: absolute; left: 29px; top: 57px;
    color: var(--white); font-weight: 300; font-size: 37px; line-height: 1.2;
  }
  .brand {
    position: absolute; left: 782px; top: 70px; width: 160px;
    display: flex; align-items: center; gap: 8px;
    color: var(--white); font-weight: 700; font-size: 21px; letter-spacing: 0.5px;
  }
  .brand-dot {
    width: 12px; height: 12px; border-radius: 50%; background: var(--orange);
    flex-shrink: 0;
  }
  .image-slot {
    position: absolute; left: 58px; top: 186px; width: 398px; height: 250px;
    background: var(--placeholder);
    display: flex; align-items: center; justify-content: center;
    color: var(--placeholder-text); font-weight: 300; font-size: 30px;
  }
  .body-copy {
    position: absolute; left: 58px; top: 472px; width: 404px;
    color: var(--body-text); font-size: 17.6px; line-height: 22.7px;
    text-align: justify;
  }
  .key-points {
    position: absolute; left: 521px; top: 216px; width: 420px;
    list-style: none;
  }
  .key-points li {
    position: relative; padding-left: 25px; margin-bottom: 29px;
    color: var(--body-text); font-size: 19px; line-height: 29px;
  }
  .key-points li::before {
    content: ""; position: absolute; left: 0; top: 10px;
    width: 10px; height: 10px; background: var(--orange);
  }
  .footer-text {
    position: absolute; left: 26px; top: 693px;
    color: var(--footer-text); font-size: 13px; line-height: 18px;
  }
  .footer-text .divider { margin: 0 6px; }
</style>
</head>
<body>
  <div class="page-label">Page 4</div>

  <section class="slide">
    <svg class="slide-chrome" width="970" height="728" viewBox="0 0 970 728" aria-hidden="true">
      <defs>
        <linearGradient id="bandGradient" x1="0" y1="0" x2="1" y2="0">
          <stop offset="0" stop-color="#e8821a"/>
          <stop offset="0.7" stop-color="#ec8a1c"/>
          <stop offset="1" stop-color="#f39a22"/>
        </linearGradient>
      </defs>
      <!-- header accent strip -->
      <polygon points="763,32 970,32 970,41.6 753,41.6" fill="var(--orange)"/>
      <!-- title band -->
      <polygon points="0,45.6 737,45.6 657,121.6 0,121.6" fill="url(#bandGradient)"/>
      <polygon points="590,45.6 737,45.6 697,83.6 540,83.6" fill="#f39a22" opacity="0.35"/>
      <!-- brand panel -->
      <polygon points="745,45.6 970,45.6 970,121.6 665,121.6" fill="var(--navy)"/>
      <!-- lower rule -->
      <polygon points="0,125.6 653,125.6 645,134.4 0,134.4" fill="var(--navy)"/>
      <!-- footer bands -->
      <polygon points="0,688 277,688 247,717 0,717" fill="var(--navy)"/>
      <polygon points="281,688 970,688 970,717 251,717" fill="var(--orange)"/>
    </svg>

    <h1 class="slide-title">Title Goes Here</h1>
    <div class="brand"><span class="brand-dot"></span>Bold Ledger</div>

    <div class="image-slot" role="img" aria-label="Placeholder area for a slide image">Image Goes Here</div>

    <p class="body-copy">Duis autem vel eum iriure dolor in hendrerit in vulputate velit esse molestie consequat, vel illum dolore eu feugiat nulla facilisis at vero eros et accumsan et iusto odio dignissim qui blandit praesent luptatum zzril delenit augue duis dolore te feugait nulla facilisi.</p>

    <ul class="key-points">
      <li>Souvlaki ignitus carborundum e pluribus unum.</li>
      <li>Defacto lingo est igpay atinlay. Marquee selectus non provisio.</li>
      <li>Quote meon an estimate et non interruptus stadium.</li>
      <li>Sic tempus fugit esperanto hiccup estrogen.</li>
      <li>Epsum factorial non deposit quid pro quo hic escorol.</li>
    </ul>

    <div class="footer-text">www.boldledger.com<span class="divider">|</span>Page 2</div>
  </section>
</body>
</html>
```